Signage Design Project - For Sale and For Rent

I am looking to revamp our For Sale and For Rent signboards.
The size of the board is
1250mm WIDTH
1800mm HEIGHT
The board is one sided, and slightly curved (will not impact the design at all)
For Rent Signs need to include the following information;
NESTor Logo
For Rent
Website
Facebook link (www.nestorsocial.example/nestorhomesco)
Phone number 6148 7309
For Sale signs need to include the following information
NESTor logo
For Sale
Website
Facebook link
Phone number 6148 7309
One signboard with Colin Partridge (this is the agents name)
One signboard with Peter Halvey (this is the agents name)
Full service real estate for a low $5,950 (+GST)
The more bold, punch and creative the better- we are very much an innovative and young company. I would suggest visiting our website, www.nestorhomes.example.au and our facebook page to get a feel for our company.
Updates
Existing signboard + logo files have been updated.
Have also guaranteed payment.
Real Estate

```html
<!DOCTYPE html>
<html lang="en">
<head>
<meta charset="utf-8">
<title>NESTor – For Sale signboard</title>
<link href="https://fonts.googleapis.com/css2?family=League+Gothic&display=swap" rel="stylesheet">
<style>
  :root {
    --backdrop: #ececec;
    --paper: #e7eee0;
    --paper-line: #dce5d3;
    --sage: #a8c49a;
    --leaf: #6b9b57;
    --ink: #111111;
    --white: #ffffff;
  }
  html, body {
    margin: 0;
    padding: 0;
    width: 1026px;
    height: 1200px;
    overflow: hidden;
    background: var(--backdrop);
  }
  .signboard {
    position: absolute;
    left: 96px;
    top: 0;
    width: 834px;
    height: 1200px;
  }
  .signboard svg {
    display: block;
    font-family: "League Gothic", "Arial Narrow", sans-serif;
  }
  .brand-name { fill: var(--ink); font-size: 82px; letter-spacing: 10px; }
  .headline { fill: var(--ink); }
  .agent-first { fill: var(--ink); }
  .agent-last { fill: var(--white); }
  .phone { fill: var(--white); }
  .website { fill: var(--leaf); }
  .social-link { fill: var(--white); letter-spacing: 1px; }
  .offer-text { fill: var(--white); }
</style>
</head>
<body>
<main class="signboard">
  <svg width="834" height="1200" viewBox="0 0 834 1200" xmlns="http://www.w3.org/2000/svg">
    <defs>
      <pattern id="paper-stripes" width="6" height="6" patternUnits="userSpaceOnUse">
        <rect width="6" height="6" fill="var(--paper)"/>
        <rect width="6" height="1.5" fill="var(--paper-line)"/>
      </pattern>
    </defs>

    <rect class="board-surface" width="834" height="1200" fill="url(#paper-stripes)"/>

    <rect class="rooftop-band" role="img" aria-label="Rooftop skyline silhouette in sage green"
          x="0" y="680" width="834" height="520" fill="var(--sage)"/>

    <g class="brand">
      <rect class="brand-square" x="250" y="70" width="40" height="40" fill="var(--leaf)"/>
      <text class="brand-name" x="310" y="118">NESTOR</text>
    </g>

    <g class="offer-badge">
      <circle cx="578" cy="518" r="88" fill="var(--sage)"/>
      <circle cx="578" cy="518" r="92" fill="none" stroke="var(--sage)" stroke-width="10" stroke-dasharray="7 7"/>
      <text class="offer-text" x="578" y="490" font-size="36" text-anchor="middle">FULL SERVICE</text>
      <text class="offer-text" x="578" y="526" font-size="36" text-anchor="middle">REAL ESTATE</text>
      <rect x="516" y="540" width="22" height="2" fill="var(--white)"/>
      <text class="offer-text" x="578" y="548" font-size="18" text-anchor="middle">FOR A LOW</text>
      <rect x="618" y="540" width="22" height="2" fill="var(--white)"/>
      <text class="offer-text" x="568" y="598" font-size="56" text-anchor="middle">$5,950</text>
      <text class="offer-text" x="624" y="566" font-size="13">+GST</text>
    </g>

    <rect class="rule" x="162" y="184" width="316" height="12" fill="var(--ink)"/>
    <text class="headline" x="162" y="446" font-size="318" textLength="316" lengthAdjust="spacingAndGlyphs">FOR</text>
    <text class="headline" x="162" y="753" font-size="374" textLength="316" lengthAdjust="spacingAndGlyphs">SALE</text>
    <rect class="rule" x="162" y="762" width="316" height="20" fill="var(--ink)"/>

    <text x="162" y="861" font-size="72" textLength="316" lengthAdjust="spacingAndGlyphs"><tspan class="agent-first">COLIN</tspan><tspan class="agent-last">PARTRIDGE</tspan></text>
    <text class="phone" x="162" y="966" font-size="128" textLength="316" lengthAdjust="spacingAndGlyphs">6148-7309</text>
    <rect class="rule" x="162" y="984" width="316" height="14" fill="var(--white)"/>
    <text class="website" x="162" y="1068" font-size="60" textLength="316" lengthAdjust="spacingAndGlyphs">NESTORHOMES.EXAMPLE.AU</text>
    <rect class="rule" x="162" y="1096" width="316" height="14" fill="var(--white)"/>

    <rect class="social-square" x="134" y="1128" width="44" height="44" rx="4" fill="var(--leaf)"/>
    <text class="social-link" x="206" y="1162" font-size="34" textLength="470" lengthAdjust="spacingAndGlyphs">WWW.NESTORSOCIAL.EXAMPLE/NESTORHOMESCO</text>
  </svg>
</main>
</body>
</html>
```